We need a wordpress design that will incorporate a professional color scheme with company logo in a clean layout. The design needs to consider that this will be developed on a responsive theme. Colors are blue and green of the logo and and an accent color (perhaps very light brown/tan). Client wants a 'modern' look.

Industry/Entity Type

It Company

Font styles to use
Serif
Sans Serif

Colors

Designer to choose colors to be used in the design.

Requirements
Must have
• navigation: 1) Home; 2) Services; 3) Auctions by Type; 4) About Us; 5) QVT Bulletin 6) Videos; 7) Contact Us

VERY general idea of layout is attached, Site will have slideshow, image is attached. Widgets used to are: 1) Email Contact Form; 2) social media icons, QT Linkora, ViewNest; 3) Featured Auctions; 4) News & Events blog; Featured Video

Footer will have affiliation logos, contact info and perhaps smaller company logo:
Phone: (512) 555-0147 / Mobile: (512) 555-0183 (Miriam)
Email: mdorrance482@mailbox-example.com / holden@parkelldorrance.example
Address: 417 FM 1382N • #B208 • PMB315 • Austin, TX 78791

Nice to have
• Use of a dropdown menu

```html
<!DOCTYPE html>
<html lang="en">
<head>
<meta charset="utf-8">
<title>Parkell-Dorrance Auction Marketing</title>
<link rel="stylesheet" href="https://fonts.googleapis.com/css2?family=Lato:wght@400;700;900&display=swap">
<style>
:root{
  --blue:#1d5e98;
  --blue-dark:#0f4a80;
  --nav-top:#2a78b8;
  --nav-bottom:#0f4f8c;
  --green:#0f7a4a;
  --teal:rgba(24,140,105,.9);
  --band:rgba(18,88,150,.88);
  --brown:#7a4e1c;
  --brown-light:rgba(140,92,38,.82);
  --text:#333;
  --muted:#777;
  --gray-band:#e6e6e6;
  --footer:#f2f2f2;
}
*{margin:0;padding:0;box-sizing:border-box}
html,body{width:880px;height:1200px;overflow:hidden;background:#fff}
body{position:relative;font-family:"Lato",sans-serif;color:var(--text)}
.abs{position:absolute}
.header-band{left:0;top:0;width:880px;height:155px;background:linear-gradient(#fdfdfd,var(--gray-band))}
.brand{left:88px;top:18px;width:130px;text-align:center;color:var(--blue);font-weight:900;line-height:1.15}
.brand .name{font-size:19px;white-space:nowrap}
.brand .sub{font-size:11.5px}
.social{display:flex;gap:4px;align-items:center}
.social span{font-size:8px;font-weight:700;color:#fff;background:var(--blue);padding:3px 4px;border-radius:2px}
.header-social{right:250px;top:70px}
.contact-top{left:642px;top:54px;color:#333}
.contact-top .phone{font-size:17px;display:flex;align-items:center;gap:4px}
.contact-top .mail{font-size:10px;margin-top:3px;display:flex;align-items:center;gap:5px}
.nav{left:86px;top:98px;width:701px;height:40px;background:linear-gradient(var(--nav-top),var(--nav-bottom));display:flex}
.nav a{color:#fff;text-decoration:none;font-size:13.5px;display:flex;align-items:center;justify-content:center;border-right:1px solid rgba(255,255,255,.25)}
.nav a:last-child{border-right:none}
.hero{left:86px;top:138px;width:701px;height:297px;background:linear-gradient(100deg,#8d8a80 0%,#b9bcb2 35%,#6f9b8c 60%,#4f7f70 80%,#a9aca3 100%);border-radius:0 0 4px 4px}
.hero-caption{left:123px;top:248px;width:251px;height:110px;background:var(--brown-light);color:#fff;padding:16px 22px}
.hero-caption h1{font-weight:400;font-size:22px;line-height:1.1}
.hero-caption h2{font-weight:400;font-size:17px;margin-top:2px}
.btn-blue{display:inline-block;background:linear-gradient(#3a8fd0,#1f6cb0);color:#fff;font-size:11px;padding:6px 15px;border-radius:2px;margin-top:10px}
.dots{left:413px;top:417px;display:flex;gap:3px}
.dots i{width:10px;height:10px;border-radius:50%;background:var(--blue-dark)}
.dots i:first-child{background:#eee}
.intro{left:88px;top:465px;color:var(--blue)}
.intro .lead{font-size:19px}
.intro .rest{font-size:14px;margin-top:6px}
.btn-brown{left:700px;top:486px;width:85px;height:25px;background:linear-gradient(#8e5d28,#5f3a12);color:#fff;font-size:10.5px;display:flex;align-items:center;justify-content:center;border-radius:2px}
.divider{left:84px;top:541px;width:705px;height:1px;background:#ddd}
.upcoming{left:85px;top:565px;width:219px;height:220px;border:1px solid #ddd;background:#fff;box-shadow:0 1px 3px rgba(0,0,0,.1)}
.upcoming .photo{position:absolute;left:10px;top:10px;width:197px;height:109px;background:linear-gradient(135deg,#5d8fd0,#2c5f9e 50%,#c9a06a)}
.upcoming h3{position:absolute;left:16px;top:130px;font-size:14px;color:var(--blue);font-weight:700}
.upcoming p{position:absolute;left:17px;top:149px;width:190px;font-size:8px;color:#666;line-height:1.7}
.btn-green{position:absolute;left:15px;top:182px;width:82px;height:24px;background:var(--green);color:#fff;font-size:9px;display:flex;align-items:center;justify-content:center;border-radius:2px}
.tile{width:207px;overflow:hidden}
.tile .photo{position:absolute;inset:0}
.tile .label{position:absolute;left:0;right:0;bottom:0;color:#fff;padding:0 15px;display:flex;flex-direction:column;justify-content:center;line-height:1.2}
.tile .label b{font-weight:400;font-size:14px}
.tile .label small{font-size:10px}
.row1{top:565px;height:102px}
.row1 .label{height:29px;background:var(--band)}
.row2{top:678px;height:103px}
.row2 .label{height:40px;background:var(--teal)}
.col2{left:332px}.col3{left:564px}
.news-title{left:88px;top:821px;font-size:19px;color:#333;font-weight:400}
.news{top:855px;width:230px}
.news h4{font-weight:400;font-size:13px;color:var(--blue)}
.news .sub{font-size:9px;color:#333;margin-top:4px}
.news p{font-size:8.5px;color:var(--muted);line-height:1.75;margin-top:8px}
.footer{left:0;top:970px;width:880px;height:165px;background:var(--footer)}
.signup{left:87px;top:1001px;width:122px;height:39px;background:var(--blue-dark);color:#fff;font-size:10.5px;display:flex;align-items:center;gap:8px;padding-left:12px;line-height:1.3}
.footer-contact{left:236px;top:1000px;font-size:9.5px;color:#555;line-height:18.4px}
.footer-social{left:235px;top:1095px}
.badges{left:515px;top:1003px;width:110px;display:grid;grid-template-columns:1fr 1fr;gap:8px}
.badges i{height:30px;background:#444;border-radius:3px}
.badges i:first-child{border-radius:50%;width:30px;margin-left:10px}
.footer-brand{left:645px;top:1008px;width:142px}
.bottom-bar{left:0;top:1135px;width:880px;height:65px;background:#fff}
.bottom-links{left:88px;top:1160px;font-size:10.5px;color:#555}
.copyright{left:528px;top:1161px;font-size:9.5px;color:#666}
</style>
</head>
<body>
<div class="abs header-band"></div>

<div class="abs brand"><div class="name">Meridian Land</div><div class="sub">Parkell-Dorrance<br>Auction Marketing</div></div>

<div class="abs social header-social"><span>ViewNest</span><span>QT</span><span>Linkora</span></div>

<div class="abs contact-top">
  <div class="phone"><svg width="16" height="16" viewBox="0 0 16 16"><circle cx="8" cy="8" r="7" fill="none" stroke="#1c8a4a" stroke-width="1.5"/><path d="M5.5 4.5l1.5 1.5-1 1c.5 1.2 1.3 2 2.5 2.5l1-1 1.5 1.5-1 1.2C7.5 11 5 8.5 4.5 6z" fill="#1c8a4a"/></svg>1-800-555-0126</div>
  <div class="mail"><svg width="12" height="9" viewBox="0 0 12 9"><rect width="12" height="9" rx="1" fill="#2a6fb0"/><path d="M0 0l6 5 6-5" fill="none" stroke="#fff"/></svg>info@meridianland.example</div>
</div>

<nav class="abs nav">
  <a style="width:114px">Services</a>
  <a style="width:154px">Auctions by Type</a>
  <a style="width:93px">About</a>
  <a style="width:128px">QVT Bulletin</a>
  <a style="width:95px">Videos</a>
  <a style="width:117px">Contact</a>
</nav>

<div class="abs hero" role="img" aria-label="Slideshow photo of an industrial machine shop with green lathes and mills"></div>
<div class="abs hero-caption">
  <h1>Making "SOLD"</h1>
  <h2>Our Specialty for 30 Years</h2>
  <span class="btn-blue">Read More</span>
</div>
<div class="abs dots"><i></i><i></i><i></i><i></i></div>

<div class="abs intro">
  <div class="lead">The go-to business asset liquidation and real estate-at-auctiuon solution</div>
  <div class="rest">provider in Texas and across the southwest for over 30 years using our proprietary QVT Process.</div>
</div>
<div class="abs btn-brown">READ MORE</div>
<div class="abs divider"></div>

<div class="abs upcoming">
  <div class="photo" role="img" aria-label="Modern glass office building against blue sky"></div>
  <h3>UPCOMING AUCTION</h3>
  <p>Lorem ipsum dolor sit amet consectetuer adipis cing elit Nam cursus Morbi ut</p>
  <span class="btn-green">More Auctions</span>
</div>

<div class="abs tile row1 col2">
  <div class="photo" role="img" aria-label="City skyline behind a row of painted houses" style="background:linear-gradient(#d8a060,#8a8aa0 55%,#5a7a9a)"></div>
  <div class="label"><b>Real Estats</b></div>
</div>
<div class="abs tile row1 col3">
  <div class="photo" role="img" aria-label="Staff sorting goods in a warehouse" style="background:linear-gradient(120deg,#c9b8a0,#6f8fb8 60%,#d8c860)"></div>
  <div class="label"><b>Business Liquidations</b></div>
</div>
<div class="abs tile row2 col2">
  <div class="photo" role="img" aria-label="Workers in hard hats inspecting an industrial site" style="background:linear-gradient(120deg,#8a6a4a,#b89870 50%,#6a7a90)"></div>
  <div class="label"><b>Commercial Industrial</b><small>&amp; Speciality Assets</small></div>
</div>
<div class="abs tile row2 col3">
  <div class="photo" role="img" aria-label="Business meeting for an appraisal" style="background:linear-gradient(120deg,#5a4a40,#9aa4b4 50%,#7a8ca0)"></div>
  <div class="label"><b>Appraisals</b></div>
</div>

<h2 class="abs news-title">News &amp; Events</h2>
<div class="abs news" style="left:88px">
  <h4>The QVT Bulletin:</h4>
  <div class="sub">Holden Dorrance Receives Lifetime Achievement Award</div>
  <p>Lorem ipsum dolor sit amet consectetuer adipiscing elit Nam cursus Morbi ut mi Nullam</p>
</div>
<div class="abs news" style="left:333px">
  <h4>Praesent elementum elit</h4>
  <div class="sub">Lorem ipsum dolor sit amet consectetuer adipiscing</div>
  <p>Lorem ipsum dolor sit amet consectetuer adipiscing elit Nam cursus Morbi ut mi Nullam</p>
</div>
<div class="abs news" style="left:573px">
  <h4>Vivamus porttitor purus</h4>
  <div class="sub">Mauris vel lacus vitae felis vestibulum</div>
  <p>Lorem ipsum dolor sit amet consectetuer adipiscing elit Nam cursus Morbi ut mi Nullam</p>
</div>

<footer>
  <div class="abs footer"></div>
  <div class="abs signup"><svg width="20" height="16" viewBox="0 0 20 16"><rect width="20" height="16" rx="2" fill="#fff"/><path d="M1 2l9 7 9-7" fill="none" stroke="#0f4a80" stroke-width="2"/></svg><span>Sign Up For<br>Auction Alerts</span></div>
  <div class="abs footer-contact">
    Phone: (512) 555-0147 / Mobile: (512) 555-0183 (Miriam)<br>
    Email: mdorrance482@mailbox-example.com /<br>
    holden@parkelldorrance.example<br>
    Address: 417 FM 1382N • #B208 •<br>
    PMB315 • Austin, TX 78791
  </div>
  <div class="abs social footer-social"><span>ViewNest</span><span>QT</span><span>Linkora</span></div>
  <div class="abs badges" aria-label="Affiliation badges"><i></i><i></i><i></i><i></i></div>
  <div class="abs brand footer-brand"><div class="name">Meridian Land</div><div class="sub">Parkell-Dorrance<br>Auction Marketing</div></div>
  <div class="abs bottom-bar"></div>
  <div class="abs bottom-links">Services &nbsp;|&nbsp; Auctions by Type &nbsp;|&nbsp; About &nbsp;|&nbsp; QVT Bulletin &nbsp;|&nbsp; Videos &nbsp;|&nbsp; Contact</div>
  <div class="abs copyright">© 2014 Company Name &nbsp;All right reserved &nbsp;Term of Use</div>
</footer>
</body>
</html>
```